New Innovative Counselling and psychotherapy Service needs Business Card design

Keep it simple and professional. On one side, just company name and logo (perhaps in all blue) and maybe a tag line.

On other side (all white) my name and Qualifications in centre

Industry/Entity Type

Health And Wellness

Contact Information for Business Card

Dara Whelby
Counsellor & Psychotherapist
BSc (Psychol.), BA, Dip. (Couns. & Psych.), PG.Cert (CBT), FGTrK, ONRE

I will also require Mobile no, Email and web site address of which I'll pass on to final designer.

Font styles to use
Sans Serif

Requirements
Must have
• My Logo Only and please use the colours in logo that is in it.
Should not have
• Any other images

```html
<!DOCTYPE html>
<html lang="en">
<head>
<meta charset="utf-8">
<title>Brightwell Lane – Business Card</title>
<link href="https://fonts.googleapis.com/css2?family=Roboto:wght@300;400;700&display=swap" rel="stylesheet">
<style>
  :root {
    --sky: #4fb6ea;
    --sky-deep: #43a9e2;
    --leaf: #8cc152;
    --paper: #ffffff;
    --paper-shade: #eef0f1;
    --backdrop: #e4e5e6;
    --ink-white: #ffffff;
  }
  * { margin: 0; padding: 0; box-sizing: border-box; }
  html, body {
    width: 1200px; height: 726px; overflow: hidden;
    background: var(--backdrop);
    font-family: "Roboto", Arial, sans-serif;
  }
  .canvas {
    position: relative; width: 1200px; height: 726px;
  }
  .card {
    position: absolute; top: 208px;
    width: 540px; height: 310px;
    box-shadow: 0 10px 24px rgba(0,0,0,0.12);
    overflow: hidden;
  }
  .card--front { left: 40px; background: var(--sky); }
  .card--back { left: 620px; background: var(--sky-deep); }

  /* front */
  .brand {
    position: absolute; left: 0; right: 0; top: 112px;
    display: flex; align-items: center; justify-content: center; gap: 16px;
  }
  .brand__dot {
    width: 52px; height: 52px; border-radius: 50%;
    background: var(--ink-white);
  }
  .brand__text { color: var(--ink-white); }
  .brand__name {
    font-weight: 300; font-size: 38px; line-height: 1; letter-spacing: 0.2px;
  }
  .brand__tagline {
    font-weight: 300; font-size: 13px; letter-spacing: 6.2px; margin-top: 6px;
  }

  /* back */
  .card__shape { position: absolute; inset: 0; }
  .back-brand {
    position: absolute; left: 30px; top: 104px; width: 200px;
    display: flex; flex-direction: column; align-items: center; gap: 12px;
  }
  .back-brand__dot {
    width: 70px; height: 70px; border-radius: 50%; background: var(--sky-deep);
  }
  .back-brand__name {
    color: var(--sky-deep); font-weight: 300; font-size: 22px;
  }
  .contact {
    position: absolute; left: 300px; top: 70px; width: 230px;
    color: var(--ink-white);
  }
  .contact__name { font-weight: 700; font-size: 21px; line-height: 1.1; }
  .contact__role, .contact__quals {
    font-weight: 400; font-size: 10.5px; line-height: 1.3;
  }
  .contact__list { list-style: none; margin-top: 18px; }
  .contact__item {
    display: flex; align-items: center; gap: 10px;
    font-size: 13px; line-height: 1.45;
  }
  .contact__icon { width: 11px; height: 11px; flex: none; }
</style>
</head>
<body>
<main class="canvas">

  <section class="card card--front" aria-label="Card front">
    <div class="brand">
      <span class="brand__dot" aria-hidden="true"></span>
      <div class="brand__text">
        <div class="brand__name">Brightwell Lane</div>
        <div class="brand__tagline">A tag line goes here</div>
      </div>
    </div>
  </section>

  <section class="card card--back" aria-label="Card back">
    <svg class="card__shape" viewBox="0 0 540 310" width="540" height="310" aria-hidden="true">
      <path d="M0 0 H198 Q300 150 258 310 H0 Z" fill="var(--leaf)" transform="translate(7 0)"/>
      <path d="M0 0 H198 Q300 150 258 310 H0 Z" fill="var(--paper)"/>
      <path d="M0 0 H120 Q180 150 150 310 H0 Z" fill="var(--paper-shade)" opacity="0.35"/>
    </svg>

    <div class="back-brand">
      <span class="back-brand__dot" aria-hidden="true"></span>
      <span class="back-brand__name">Brightwell Lane</span>
    </div>

    <div class="contact">
      <h1 class="contact__name">Dara Whelby</h1>
      <p class="contact__role">Counsellor &amp; Psychotherapist</p>
      <p class="contact__quals">BSc (Psychol.), BA, Dip. (Couns. &amp; Psych.),<br>PG Cert (CBT), FGTrK, ONRE</p>
      <ul class="contact__list">
        <li class="contact__item">
          <svg class="contact__icon" viewBox="0 0 12 12" aria-hidden="true"><path d="M1 3 Q6 0 11 3 L10 5 L8 4 L8 3 Q6 2 4 3 L4 4 L2 5 Z M3 6 H9 L10 11 H2 Z" fill="#fff"/></svg>
          <span>0123 456 7891</span>
        </li>
        <li class="contact__item">
          <svg class="contact__icon" viewBox="0 0 12 12" aria-hidden="true"><rect x="0.5" y="2.5" width="11" height="7" fill="#fff"/><path d="M0.5 2.5 L6 7 L11.5 2.5" fill="none" stroke="#43a9e2" stroke-width="1"/></svg>
          <span>dara.w@BrightwellLane.com</span>
        </li>
        <li class="contact__item">
          <svg class="contact__icon" viewBox="0 0 12 12" aria-hidden="true"><circle cx="6" cy="6" r="5" fill="none" stroke="#fff" stroke-width="1.2"/><ellipse cx="6" cy="6" rx="2.2" ry="5" fill="none" stroke="#fff" stroke-width="1"/><path d="M1 6 H11" stroke="#fff" stroke-width="1"/></svg>
          <span>www.BrightwellLane.com</span>
        </li>
      </ul>
    </div>
  </section>

</main>
</body>
</html>
```